Counseling Practice Business Card

I need a professional looking business card incorporating my new logo that was just completed. Card needs to incorporate my name and title, description of my specialty, my address, my phone number, my fax number, my email and my website URL. I need to be able to choose design on/with different paper colors and textures.
I do not have a lot of business card ideas so I am open to anything but I want bold,sharp, clear card without additional designs other than my logo (see attached file info). I am open to different color backgrounds or paper colors including black. I do not like traditional brackets around area codes in phone number or dashes between numbers in phone number. Am open to other ways of presenting including periods between numbers as appropriate. I do not know enough to know what I like yet but I want card to coordinate and work together with my logo. My practice emphasizes natural mental health interventions so any use of color (with background paper color or the blue and green in my logo) that elicits nature is nice. In addition to black, any natural brown or wood looking background might be desirable also. Most of the offerings so far look very similar and boring.

Target Market(s)

Potential therapy clients and other professionals

Contact Information for Business Card

Card information:
Gerald M. Whitcombe, Ph.D.
Licensed Clinical Psychologist
Integrative Health Coach
4812 Marlowe Ridge Blvd SE
Suite 310
Duluth, GA 30096
(770) 415-2983 phone
(770) 581-4096 fax
drgeraldwhitcombe@quillmarsh.net
brightfernwellness.net

Font styles to use
Serif
Sans Serif
Other font styles liked:
• anything that you think looks crisp, clear and easily readable

Requirements
Must have
• Any color used should coordinate with my logo design (see attached files).
• Card should be printed horizontally so top and bottom are longest sides of rectangle.
• Background color or paper color should complement and highlight logo. Do not like a white background. black, grey, brown or any color my logo would blend well with.
Nice to have
• I would like designer to utilize color to highlight letters/name or phone-fax-web symbols.
• Bottom edge of card could be highlighted if appropriate to an idea.
Should not have
• I would NOT want the card to have a pure white background at all.
• No clear cards.
• Cards should be oriented with long sides on bottom and top, NOT sides. DO NOT LIKE THIS THIN TALL ORIENTATION.

```html
<!DOCTYPE html>
<html lang="en">
<head>
<meta charset="utf-8">
<title>Brightfern Wellness – Business Card</title>
<link rel="stylesheet" href="https://fonts.googleapis.com/css2?family=Roboto:wght@400;500;700&display=swap">
<style>
  :root {
    --backdrop: #202022;
    --card: #141415;
    --card-edge: #1d1d1f;
    --blue: #1f7fd0;
    --white: #f4f4f4;
    --rule: #e9e9e9;
  }
  * { margin: 0; padding: 0; box-sizing: border-box; }
  html, body { width: 1200px; height: 900px; overflow: hidden; }
  body {
    background: var(--backdrop);
    font-family: "Roboto", Arial, sans-serif;
    color: var(--white);
    position: relative;
  }
  .card {
    position: absolute;
    left: 250px;
    width: 700px;
    height: 400px;
    background: linear-gradient(135deg, var(--card-edge), var(--card) 60%);
    border-radius: 3px;
  }
  .card--front { top: 30px; }
  .card--back { top: 470px; }

  .brand {
    position: absolute;
    display: flex;
    align-items: center;
    gap: 14px;
    color: var(--blue);
    font-weight: 700;
    white-space: nowrap;
  }
  .brand__dot {
    background: var(--blue);
    border-radius: 50%;
    flex: none;
  }
  .card--front .brand {
    left: 50%; top: 50%;
    transform: translate(-50%, -50%);
    font-size: 50px;
  }
  .card--front .brand__dot { width: 30px; height: 30px; }
  .card--back .brand {
    left: 40px; top: 150px;
    font-size: 27px;
    gap: 10px;
  }
  .card--back .brand__dot { width: 18px; height: 18px; }

  .divider {
    position: absolute;
    left: 335px; top: 50px;
    width: 2px; height: 240px;
    background: var(--rule);
  }
  .details {
    position: absolute;
    left: 355px; top: 48px;
    right: 20px;
  }
  .details__name {
    color: var(--blue);
    font-size: 24px;
    font-weight: 700;
    line-height: 1.1;
    white-space: nowrap;
  }
  .details__title, .details__address {
    font-size: 17px;
    font-weight: 500;
    line-height: 1.3;
  }
  .details__title { margin-top: 2px; }
  .details__address { margin-top: 10px; }
  .contact { list-style: none; margin-top: 14px; }
  .contact__item {
    display: flex;
    align-items: center;
    gap: 10px;
    font-size: 17px;
    font-weight: 500;
    line-height: 1.35;
    white-space: nowrap;
  }
  .contact__icon { width: 13px; height: 13px; flex: none; fill: var(--blue); }
  .contact__accent { color: var(--blue); }
</style>
</head>
<body>
  <section class="card card--front" aria-label="Card front">
    <div class="brand"><span class="brand__dot"></span>Brightfern Wellness</div>
  </section>

  <section class="card card--back" aria-label="Card back">
    <div class="brand"><span class="brand__dot"></span>Brightfern Wellness</div>
    <div class="divider"></div>
    <div class="details">
      <h1 class="details__name">Gerald M. Whitcombe, Ph.D.</h1>
      <p class="details__title">Licensed Clinical Psychologist<br>Integrative Health Coach</p>
      <p class="details__address">4812 Marlowe Ridge Blvd SE<br>Suite 310 Duluth, GA 30096</p>
      <ul class="contact">
        <li class="contact__item">
          <svg class="contact__icon" viewBox="0 0 16 16" aria-hidden="true"><path d="M3.5 1l2.5 3-1.5 1.8c.9 2 2.6 3.7 4.6 4.6L10.9 9l3 2.5-1.6 2.8C7 14 2 9 1.7 3.6z"/></svg>
          (770) 415-2983
        </li>
        <li class="contact__item">
          <svg class="contact__icon" viewBox="0 0 16 16" aria-hidden="true"><path d="M4 1h8v4H4zM1 6h14v6h-3v3H4v-3H1zm4 4v3h6v-3z"/></svg>
          (770) 581-4096
        </li>
        <li class="contact__item">
          <svg class="contact__icon" viewBox="0 0 16 16" aria-hidden="true"><path d="M1 3h14v10H1zm1.5 1.5v.4L8 8.8l5.5-3.9v-.4zm0 2.2v4.8h11V6.7L8 10.6z"/></svg>
          drgeraldwhitcombe@quillmarsh.net
        </li>
        <li class="contact__item">
          <svg class="contact__icon" viewBox="0 0 16 16" aria-hidden="true"><path d="M8 1a7 7 0 1 0 0 14A7 7 0 0 0 8 1zm0 1.5c.8 0 1.7 1.5 2 4H6c.3-2.5 1.2-4 2-4zM2.6 6.5h2c0-1.4.3-2.6.7-3.4A5.6 5.6 0 0 0 2.6 6.5zm8.8 0h2a5.6 5.6 0 0 0-2.7-3.4c.4.8.7 2 .7 3.4zM2.6 9.5a5.6 5.6 0 0 0 2.7 3.4c-.4-.8-.7-2-.7-3.4zm3.4 0c.3 2.5 1.2 4 2 4s1.7-1.5 2-4zm5.4 0c0 1.4-.3 2.6-.7 3.4a5.6 5.6 0 0 0 2.7-3.4zM2.5 8h11v0z"/></svg>
          <span>www.<span class="contact__accent">brightfernwellness</span>.net</span>
        </li>
      </ul>
    </div>
  </section>
</body>
</html>
```